Law Firm Web Design Project

I need a website design for my law firm. I have attached to this description the URL of a website I liked with a description of the elements of that website that appeal to me.

I am also attaching my law firm's logo, so you can review that design when you create the website design.

Reference Site: www.harborfieldcounsel-example.com

What we like about this site:
• The different layers
• Subtle designs, textures, curves
• 3 dimensional
• Floating effect
• Simple logo that stands out (we are providing logo)
• Prominent phone number
• Location of Areas of Practice
oDivorce, Legal Separation, Paternity, Spousal Maintenance, Child Custody, Child Support, Protective Orders, Community Property, Business Evaluations
• The limited amount of links across the top
o Home, Meet Our Attorney, FAQ, Contact Us
• Request A Consultation click through
• Right side bar with the moving icons
• Badges

Other Tips:
• We don’t want the website to be dark. The logo can standout and the website can have its own colors and flow.
• We would like there to be a “call to action” or way to get in touch on every page and every page view
• We would like a place for credit card icons at the bottom of the page
• Strong, yet elegant
• Finally, just use the website provided as a guide. Explore different colors, textures, shapes, shadows etc.
Updates

I would prefer the website have colors that are complementary to my logo and that are strong and elegant.  I like black, gold, amber, and tan colors.  Black should be used sparingly as an accent only, since I don't want the website to be too dark.

Please review the website I provided as an example in my project description.  I really like the three dimensional aspects of that website (web page floating on top of a background and the logo in the upper left floating on top of the web page).  I also like the use of "swirling" on the background and the webpage.  I hope this additional information is helpful.

Requirements
Must have
• I need a place to insert "client testimonials", a place to insert four logos of awards the law firm has received, a place for people to fill out a form to contact the law firm via email, and a place for people to click to review articles I have written.

```html
<!DOCTYPE html>
<html lang="en">
<head>
<meta charset="utf-8">
<title>Ashcombe Law</title>
<link rel="stylesheet" href="https://fonts.googleapis.com/css2?family=Libre+Baskerville:wght@400;700&family=Rosario:wght@400;600&family=Cabin:wght@400;600&display=swap">
<style>
:root{
  --amber:#c8652a;
  --amber-dark:#a54f1e;
  --cream:#efe7d3;
  --tan:#d9c398;
  --tan-light:#ddc9a1;
  --side:#e7dec2;
  --ink:#3a3836;
  --ink-deep:#2b2a28;
  --gold:#9a8a3e;
  --gold-soft:#e0c98a;
  --brown:#5a4a36;
  --heading:#8c7a62;
  --body:#5e5142;
  --link:#c06a3a;
  --button:#c0754a;
  --submit:#3d5a9e;
}
*{box-sizing:border-box;margin:0;padding:0}
html,body{width:1044px;height:1200px;overflow:hidden}
body{font-family:"Rosario",sans-serif;background:var(--amber)}
.canvas{position:relative;width:1044px;height:1200px;overflow:hidden;
  background:
    linear-gradient(90deg,rgba(0,0,0,.12),rgba(255,255,255,.08) 6%,rgba(0,0,0,.08) 11%,transparent 15%,transparent 85%,rgba(0,0,0,.08) 89%,rgba(255,255,255,.08) 94%,rgba(0,0,0,.12)),
    linear-gradient(180deg,#d0702f,#c25f26 60%,#b9571f);}
.page{position:absolute;left:153px;top:0;width:738px;height:1200px;box-shadow:0 0 14px rgba(0,0,0,.45)}
.abs{position:absolute}

/* header */
.header{left:0;top:0;width:738px;height:124px;background:linear-gradient(180deg,#f3ecda,var(--cream) 70%,#e8dcc0)}
.brand-mark{left:17px;top:24px;width:62px;height:62px;background:var(--ink-deep)}
.brand-rule{left:104px;top:36px;width:1px;height:80px;background:#cdbf9f}
.brand-name{left:121px;top:34px;font-family:"Libre Baskerville",serif;font-size:42px;color:var(--gold);letter-spacing:.5px}
.brand-sub{left:121px;top:82px;width:246px;display:flex;align-items:center;gap:8px;font-family:"Libre Baskerville",serif;font-size:17px;color:var(--ink)}
.brand-sub::before,.brand-sub::after{content:"";flex:1;height:1px;background:#a9b0c6}
.call{left:447px;top:34px;font-family:"Cabin",sans-serif;font-size:13px;color:var(--amber-dark)}
.call strong{font-weight:400;font-size:25px;color:#4a4642;margin-left:4px;font-family:"Rosario",sans-serif}
.nav{left:400px;top:94px;width:338px;height:30px;display:flex;align-items:center;justify-content:flex-end;padding-right:8px;font-family:"Cabin",sans-serif;font-size:11.3px;white-space:nowrap}
.nav a{color:#f1ead9;text-decoration:none;padding:0 6px;border-left:1px solid #6a6560;line-height:20px}
.nav a:first-child{border-left:0;color:#e0a35a}

/* hero */
.hero{left:0;top:124px;width:738px;height:263px;background:
  linear-gradient(180deg,#42524a 0%,#5f7a72 22%,#8aa59c 38%,#c9cfc2 55%,#d9cdb3 70%,#cbb797 100%)}
.hero-base{left:0;top:386px;width:738px;height:4px;background:#4b4844}
.dots{left:57px;top:365px;display:flex;gap:6px}
.dots span{width:13px;height:13px;border-radius:50%;background:#fff;border:1px solid #b8b0a4}
.dots span:first-child{background:var(--amber)}
.promo{left:559px;top:290px;width:190px;height:101px;background:#f2ecdd;border-radius:8px 0 8px 8px;box-shadow:0 3px 8px rgba(0,0,0,.35);padding:10px 0 0 20px}
.promo h2{font-family:"Libre Baskerville",serif;font-weight:400;font-size:23px;color:var(--ink-deep);line-height:1.1}
.promo p{font-family:"Libre Baskerville",serif;font-size:9.5px;color:#4a433b;line-height:15px;margin-top:4px}
.promo-btn{left:570px;top:362px;width:169px;height:23px;background:var(--button);color:#fff;font-family:"Libre Baskerville",serif;font-size:12.5px;text-align:center;line-height:23px;border-radius:2px}

/* content */
.content{left:0;top:390px;width:738px;height:610px;background:var(--tan)}
.main-panel{left:158px;top:0;width:440px;height:607px;background:var(--tan-light);border-radius:0 34px 0 0;box-shadow:3px 0 3px rgba(120,90,50,.35)}
.left-rule{left:158px;top:22px;width:1px;height:585px;background:#a89272}
.side-right{left:598px;top:0;width:140px;height:607px;background:var(--side)}
.tab{height:25px;background:var(--ink);color:#f1ead9;font-family:"Cabin",sans-serif;font-size:10.5px;line-height:27px;letter-spacing:.3px;border-radius:0 8px 0 0;white-space:nowrap}
.tab.left{left:0;width:158px;padding-left:18px}
.tab.right{left:613px;width:125px;text-align:center;border-radius:8px 0 0 0}
.practice{left:24px;top:444px;list-style:none;font-size:9.3px;color:var(--brown);line-height:19.1px}
.qc-text{left:26px;top:688px;font-size:8px;color:var(--brown);line-height:12.5px;white-space:nowrap}
.field{left:24px;width:115px;height:16px;background:#fff;border:1px solid #cbb896;border-radius:2px;font-size:8px;color:#7a6c5a;padding:3px 8px}
.field.area{height:77px}
.submit{left:82px;top:860px;width:57px;height:15px;background:var(--submit);color:#fff;font-family:"Cabin",sans-serif;font-weight:600;font-size:9.5px;text-align:center;line-height:15px;border-radius:2px}

.welcome{left:219px;top:420px;width:340px}
.welcome h1{font-family:"Libre Baskerville",serif;font-weight:400;font-size:23px;color:var(--heading);margin-bottom:12px}
.welcome p{font-size:11.5px;line-height:19.6px;color:var(--body);letter-spacing:.4px;margin-bottom:19px}
.welcome ul{list-style:none;margin:-4px 0 19px 0}
.welcome li{font-size:11.5px;line-height:19.6px;color:var(--body);letter-spacing:.4px;padding-left:17px;position:relative}
.welcome li::before{content:"";position:absolute;left:2px;top:7px;width:6px;height:6px;border-radius:50%;background:#6a645c}
.content-rule{left:221px;top:861px;width:340px;height:1px;background:linear-gradient(90deg,transparent,#b0875a 20%,#b0875a 80%,transparent)}
.badge{top:896px;height:68px;border-radius:3px}
.badge-a{left:217px;width:100px;background:#b8b8d0;opacity:.55}
.badge-b{left:341px;width:43px;background:#f6f4ee;border:2px solid #2f6fa0}
.badge-c{left:411px;width:129px;background:#efe6d6;border-top:3px solid #d0343a}

.aside-item{left:662px;width:66px;font-size:7.6px;line-height:12.2px;color:var(--brown);white-space:nowrap}
.aside-item a{display:block;margin-top:6px;color:var(--link);text-decoration:none}
.aside-rule{left:612px;width:126px;height:1px;background:#b99a78}
.icon{left:617px;width:32px;height:42px;border-radius:3px}

/* footer */
.footer{left:0;top:1000px;width:738px;height:200px;background:var(--ink)}
.foot-links{left:32px;top:1025px;font-family:"Cabin",sans-serif;font-size:8.5px;color:#d8d2c8}
.foot-links span{padding:0 4px;color:#8a857e}
.foot-text{left:33px;top:1046px;font-family:"Libre Baskerville",serif;font-size:8.8px;line-height:13.5px;color:var(--gold-soft)}
.foot-rule{left:0;top:1094px;width:528px;height:1px;background:#55524e}
.copy{left:32px;top:1114px;font-family:"Cabin",sans-serif;font-size:8.6px;color:#d8d2c8}
.accept{left:322px;top:1115px;font-family:"Libre Baskerville",serif;font-weight:700;font-size:9.5px;color:#cfc8bc}
.cards{left:288px;top:1133px;display:flex;gap:1px}
.cards span{width:40px;height:24px;border-radius:2px}
.foot-mark{left:528px;top:1038px;width:36px;height:36px;background:#f0e6c8}
.foot-rule-v{left:574px;top:1034px;width:1px;height:44px;background:#7a766f}
.foot-name{left:580px;top:1036px;font-family:"Libre Baskerville",serif;font-size:21px;color:var(--gold)}
.foot-law{left:580px;top:1060px;width:131px;display:flex;align-items:center;gap:5px;font-family:"Libre Baskerville",serif;font-size:9px;color:#d8d2c8}
.foot-law::before,.foot-law::after{content:"";flex:1;height:1px;background:#8a857e}
.foot-phone{left:580px;top:1074px;font-size:20px;color:#ece6da}
.foot-addr{left:570px;top:1097px;width:160px;text-align:center;font-size:8px;line-height:11px;color:#d8d2c8}
</style>
</head>
<body>
<div class="canvas">
  <div class="page">

    <header class="abs header">
      <svg class="abs" style="left:0;top:0" width="738" height="124" viewBox="0 0 738 124" aria-hidden="true">
        <defs>
          <linearGradient id="swirl" x1="0" y1="0" x2="1" y2="1">
            <stop offset="0" stop-color="#e9dec3"/>
            <stop offset=".5" stop-color="#f4eedf"/>
            <stop offset="1" stop-color="#ddcfae"/>
          </linearGradient>
        </defs>
        <path d="M385 0 H738 V124 H420 C396 108 378 80 372 50 C372 30 378 12 385 0 Z" fill="url(#swirl)"/>
        <path d="M390 94 H738 V124 H420 C406 116 396 106 390 94 Z" fill="#2d2b29"/>
        <path d="M386 90 H738 V94 H390 Z" fill="#c8652a"/>
      </svg>
      <div class="abs brand-mark"></div>
      <div class="abs brand-rule"></div>
      <div class="abs brand-name">Ashcombe</div>
      <div class="abs brand-sub">LAW</div>
      <div class="abs call">Call Today: <strong>123.456.7890</strong></div>
      <nav class="abs nav">
        <a href="#">Home</a><a href="#">Meet our Attorneys</a><a href="#">Resources</a><a href="#">FAQ</a><a href="#">Contact</a>
      </nav>
    </header>

    <div class="abs hero" role="img" aria-label="Photo of a smiling family walking barefoot along a sandy beach by the sea"></div>
    <div class="abs hero-base"></div>
    <div class="abs dots"><span></span><span></span><span></span><span></span></div>
    <div class="abs promo">
      <h2>Lorem Ipsum</h2>
      <p>Praesent justo dolor,<br>lobortis quis, lobortis dignissim.</p>
    </div>
    <div class="abs promo-btn">Consult Us Now!</div>

    <section class="abs content"></section>
    <div class="abs main-panel" style="top:390px"></div>
    <div class="abs left-rule" style="top:412px"></div>
    <div class="abs side-right" style="top:390px"></div>

    <!-- left column -->
    <div class="abs tab left" style="top:412px">AREAS OF PRACTICE</div>
    <ul class="abs practice">
      <li>Divorce</li><li>Legal Separation</li><li>Paternity</li><li>Spousal Maintenance</li><li>Child Custody</li><li>Child Support</li><li>Protective Orders</li><li>Community Property</li><li>Business Evaluations</li>
    </ul>
    <div class="abs tab left" style="top:651px;padding-left:26px">QUICK CONTACT</div>
    <p class="abs qc-text">Aliquam congue fermentum nisl.<br>Mauris accumsan nulla vel diam.</p>
    <div class="abs field" style="top:716px">Name</div>
    <div class="abs field" style="top:735px">Phone</div>
    <div class="abs field" style="top:754px">Email</div>
    <div class="abs field area" style="top:773px">About your case...</div>
    <div class="abs submit">Submit</div>

    <!-- main column -->
    <article class="abs welcome">
      <h1>Welcome to Ashcombe</h1>
      <p>Aliquam congue fermentum nisl. Mauris accumsan nulla<br>vel diam. Sed in lacus ut enim adipiscing aliquet.</p>
      <p>Nulla venenatis. In pede mi, aliquet sit amet, euismod in, auctor ut, ligula. Aliquam dapibus tincidunt metus. Praesent justo dolor, lobortis quis, lobortis dignissim, pulvinar ac, lorem. Vestibulum sed ante. Donec sagittis euismod purus.</p>
      <ul>
        <li>Praesent justo dolor</li>
        <li>Donec sagittis euismod purus</li>
        <li>Mauris accumsan nulla vel diam</li>
      </ul>
      <p>Aliquam congue fermentum nisl. Mauris accumsan nulla<br>vel diam. Sed in lacus ut enim adipiscing aliquet.</p>
      <p>Nulla venenatis. In pede mi, aliquet sit amet, euismod in, auctor ut, ligula. Aliquam dapibus tincidunt metus. Praesent justo dolor, lobortis quis, lobortis dignissim, pulvinar ac, lorem. Vestibulum sed ante. Donec sagittis euismod purus.</p>
    </article>
    <div class="abs content-rule"></div>
    <div class="abs badge badge-a"></div>
    <div class="abs badge badge-b"></div>
    <div class="abs badge badge-c"></div>

    <!-- right column -->
    <div class="abs tab right" style="top:412px">CLICK TO CALL</div>
    <svg class="abs" style="left:619px;top:449px" width="28" height="48" viewBox="0 0 28 48" role="img" aria-label="Phone icon">
      <rect x="1" y="1" width="26" height="46" rx="4" fill="#3c3c3c"/>
      <rect x="4" y="6" width="20" height="18" rx="1" fill="#5aa0d8"/>
      <g fill="#888"><rect x="5" y="28" width="5" height="3"/><rect x="12" y="28" width="5" height="3"/><rect x="19" y="28" width="5" height="3"/><rect x="5" y="34" width="5" height="3"/><rect x="12" y="34" width="5" height="3"/><rect x="19" y="34" width="5" height="3"/><rect x="5" y="40" width="5" height="3"/><rect x="12" y="40" width="5" height="3"/><rect x="19" y="40" width="5" height="3"/></g>
    </svg>
    <div class="abs aside-item" style="top:450px">Aliquam congue<br>fermentum nisl.<br>Mauris accumsan<br>nulla vel diam.<a href="#">Click here &gt;&gt;</a></div>
    <div class="abs aside-rule" style="top:526px"></div>

    <div class="abs tab right" style="top:537px">AWARDS</div>
    <div class="abs icon" style="top:573px;background:linear-gradient(180deg,#e4c45a,#a8842a)" role="img" aria-label="Gold trophy illustration"></div>
    <div class="abs aside-item" style="top:570px">Aliquam congue<br>fermentum nisl.<br>Mauris accumsan<br>nulla vel diam.<a href="#">Click here &gt;&gt;</a></div>
    <div class="abs aside-rule" style="top:645px"></div>

    <div class="abs tab right" style="top:656px">TESTIMONIALS</div>
    <div class="abs icon" style="top:694px;height:36px;background:linear-gradient(180deg,#dfe6ee,#b8c6d6)" role="img" aria-label="Notepad with pen illustration"></div>
    <div class="abs aside-item" style="top:688px">Aliquam congue<br>fermentum nisl.<br>Mauris accumsan<br>nulla vel diam.<a href="#">Click here &gt;&gt;</a></div>
    <div class="abs aside-rule" style="top:763px"></div>

    <div class="abs tab right" style="top:779px">CASE EVALUATION</div>
    <div class="abs icon" style="top:814px;height:44px;background:linear-gradient(180deg,#f4f0e2,#e6d48a);border:2px solid #2c4a7a" role="img" aria-label="Clipboard with pencil illustration"></div>
    <div class="abs aside-item" style="top:811px">Aliquam congue<br>fermentum nisl.<br>Mauris accumsan<br>nulla vel diam.<a href="#">Click here &gt;&gt;</a></div>
    <div class="abs aside-rule" style="top:886px"></div>

    <!-- footer -->
    <footer class="abs footer"></footer>
    <div class="abs foot-links">Ashcombe Law<span>|</span>Contact Us<span>|</span>Resources<span>|</span>Privacy Policy<span>|</span>Site Map</div>
    <p class="abs foot-text">Aliquam congue fermentum nisl. Mauris accumsan nulla vel diam. Sed in lacus ut enim adipiscing aliquet.<br>Praesent justo dolor, lobortis quis, lobortis dignissim, pulvinar ac, lorem.</p>
    <div class="abs foot-rule"></div>
    <div class="abs copy">Copyright © 2012.&nbsp; Ashcombe Law.&nbsp; All Rights Reserved.</div>
    <div class="abs accept">We proudly accept</div>
    <div class="abs cards">
      <span style="background:#3f86c4"></span><span style="background:#e8e4da"></span><span style="background:#d8453a"></span><span style="background:#f2f0ea"></span>
    </div>
    <div class="abs foot-mark"></div>
    <div class="abs foot-rule-v"></div>
    <div class="abs foot-name">Ashcombe</div>
    <div class="abs foot-law">LAW</div>
    <div class="abs foot-phone">123.456.7890</div>
    <div class="abs foot-addr">48 Linden Court, Suite 12<br>Fairhaven, Maryland 20322</div>

  </div>
</div>
</body>
</html>
```